KRT Project Signage

Need a sign to be displayed in the front of properties currently under Construction or Renovation to advertise our company information. Need it to be Professional and Contemporary. We are a Design/Build Construction Company. Information should include Company Name, email, website, phone number. Attached: Logo and company brochure, also included and inspiration images

```html
<!DOCTYPE html>
<html lang="en">
<head>
<meta charset="utf-8">
<title>KRT Project Signage</title>
<link href="https://fonts.googleapis.com/css2?family=Montserrat:wght@500;600;700&display=swap" rel="stylesheet">
<style>
  :root {
    --ink: #2f2f2f;
    --muted: #7a7a7a;
    --paper: #ffffff;
    --backdrop: #e9eaec;
  }
  * { margin: 0; padding: 0; box-sizing: border-box; }
  html, body {
    width: 1200px;
    height: 1200px;
    overflow: hidden;
    background: var(--backdrop);
    font-family: "Montserrat", sans-serif;
    color: var(--ink);
  }
  .sign {
    position: absolute;
    left: 178px;
    top: 41px;
    width: 845px;
    height: 1118px;
    background: var(--paper);
    border: 9px solid var(--ink);
    overflow: hidden;
  }
  .sign__swoosh {
    position: absolute;
    left: 0;
    top: 0;
    width: 100%;
    height: 100%;
  }
  .brand {
    position: absolute;
    top: 92px;
    left: 0;
    width: 100%;
    text-align: center;
  }
  .brand__name {
    font-weight: 500;
    font-size: 41px;
    letter-spacing: 1px;
    color: var(--ink);
    line-height: 1;
  }
  .brand__tagline {
    margin-top: 16px;
    font-weight: 500;
    font-size: 25px;
    letter-spacing: 1px;
    color: var(--muted);
    line-height: 1;
  }
  .rule {
    position: absolute;
    left: 130px;
    width: 622px;
    height: 3px;
    background: var(--ink);
  }
  .rule--top { top: 263px; }
  .rule--bottom { top: 589px; }
  .headline {
    position: absolute;
    top: 282px;
    left: 0;
    width: 100%;
    text-align: center;
    font-weight: 600;
    font-size: 66px;
    line-height: 72px;
    letter-spacing: 2px;
    text-transform: uppercase;
  }
  .phone {
    position: absolute;
    top: 623px;
    left: 0;
    width: 100%;
    display: flex;
    justify-content: center;
    align-items: center;
    gap: 26px;
  }
  .phone__icon { width: 88px; height: 88px; flex: none; }
  .phone__number {
    font-weight: 700;
    font-size: 80px;
    letter-spacing: -1px;
    line-height: 1;
  }
  .contact {
    position: absolute;
    left: 0;
    width: 100%;
    text-align: center;
    font-weight: 500;
    line-height: 1;
  }
  .contact--email { top: 737px; font-size: 31px; letter-spacing: 1px; text-transform: uppercase; }
  .contact--address { top: 795px; font-size: 29px; line-height: 39px; font-weight: 600; }
  .website {
    position: absolute;
    bottom: 46px;
    left: 0;
    width: 100%;
    text-align: center;
    font-weight: 600;
    font-size: 29px;
    letter-spacing: 2px;
    color: var(--paper);
    text-transform: uppercase;
  }
</style>
</head>
<body>
  <main class="sign">
    <svg class="sign__swoosh" viewBox="0 0 827 1100" preserveAspectRatio="none" aria-hidden="true">
      <path d="M0,840 Q380,1010 827,752 L827,1100 L0,1100 Z" fill="var(--ink)"/>
      <path d="M0,872 Q400,1065 827,800 L827,830 Q420,1120 0,895 Z" fill="var(--paper)"/>
    </svg>

    <header class="brand">
      <p class="brand__name">KRT CONSTRUCTION &amp; DESIGN</p>
      <p class="brand__tagline">LUXURY RENOVATIONS</p>
    </header>

    <div class="rule rule--top"></div>
    <h1 class="headline">High-End<br>Construction<br>&amp; Luxury<br>Renovations</h1>
    <div class="rule rule--bottom"></div>

    <div class="phone">
      <svg class="phone__icon" viewBox="0 0 100 100" aria-hidden="true">
        <circle cx="50" cy="50" r="50" fill="var(--ink)"/>
        <path d="M34 24c3-2 6-1 7 2l4 9c1 3 0 5-2 7l-3 3c3 7 8 12 15 15l3-3c2-2 4-3 7-2l9 4c3 1 4 4 2 7l-4 6c-2 3-6 4-10 3-18-5-31-18-36-36-1-4 0-8 3-10z" fill="var(--paper)"/>
      </svg>
      <span class="phone__number">555-014-2290</span>
    </div>

    <p class="contact contact--email">info@krtconstruction.com</p>
    <p class="contact contact--address">1480 Harbor View Blvd., Ste. 310<br>Coral Shores, FL 33499</p>

    <p class="website">www.krtconstruction.com</p>
  </main>
</body>
</html>
```